NZ First of it's kind solutions directory and marketplace for busy Mums needs a business card design

We need a business card design for our new nationwide business in NZ (long term plans to go global). We provide solutions to the everyday challenges that busy Mums face by connecting them with quality communities and suppliers of carefully selected, relevant products and services. We sell direct via our online marketplace. The final design should communicate our values of inclusivity, quality and smart solutions. Colours should incorporate our logo colour palette of #477077 and #6ba8b2. Our website is at https://www.brightnestmums.example

Target Market(s)

busy Mums, Age 28 – 50, female, income over $100K, location main centres NZ primarily but NZ wide. Is likely juggling work or career with a young family. Probably had hobbies which have fallen by the wayside.
-Wants to succeed in her chosen career without compromising on family life
-to successfully juggle her career without feeling like she is compromising her children
- Is time poor, something always has to give and it’s generally her health (she’ll stay up late, get stressed)
- probably ex corporate or professional career. Has discretional income

Industry/Entity Type

Business

Contact Information for Business Card

Lena Forbisher, Founder, BrightNestMums.example (Strapline Tap; Gather; Sorted), 47 Kowhai Terrace, Ellerslie, Auckland 1051, New Zealand. Mob: 021 483 517 Ph: +64 (0)9 571 4860

Font styles to use
Other font styles liked:
• Raleway, and/or Architects Daughter

Colors
00a990
33b8a4
86cfc6
cfeae6

Requirements
Must have
• the above details, streamline. the logo and colours associated with those logos
Should not have
• foil or metallic colours

```html
<!DOCTYPE html>
<html lang="en">
<head>
<meta charset="utf-8">
<title>BrightNest Mums – Business Card</title>
<link rel="stylesheet" href="https://fonts.googleapis.com/css2?family=Rubik:wght@500&family=Roboto:ital,wght@0,400;1,400&display=swap">
<style>
  :root {
    --page-bg: #e4e5e5;
    --teal-deep: #436a72;
    --teal-light: #6ba8b2;
    --card-white: #f7f7f7;
    --ink: #3a3d3f;
    --tagline: #dbe8ea;
    --icon: #4a6f76;
  }
  * { margin: 0; padding: 0; box-sizing: border-box; }
  html, body { width: 1200px; height: 576px; overflow: hidden; }
  body {
    position: relative;
    background: var(--page-bg);
    font-family: "Roboto", Arial, sans-serif;
  }
  .card {
    position: absolute;
    top: 138px;
    width: 484px;
    height: 292px;
    border-radius: 16px;
    overflow: hidden;
  }
  /* Front */
  .card-front {
    left: 82px;
    background: var(--teal-deep);
    color: #fff;
    text-align: center;
  }
  .brand-name {
    position: absolute;
    left: 0; right: 0;
    top: 108px;
    font-family: "Rubik", Arial, sans-serif;
    font-weight: 500;
    font-size: 44px;
    letter-spacing: -0.5px;
    color: #fff;
  }
  .strapline {
    position: absolute;
    left: 0; right: 0;
    top: 167px;
    font-size: 14px;
    letter-spacing: 5px;
    color: var(--tagline);
  }
  /* Back */
  .card-back {
    left: 602px;
    background: var(--card-white);
  }
  .back-panel { position: absolute; left: 0; top: 0; }
  .contact-block {
    position: absolute;
    right: 25px;
    top: 0;
    text-align: right;
    color: var(--ink);
  }
  .person-name {
    margin-top: 26px;
    font-family: "Rubik", Arial, sans-serif;
    font-weight: 500;
    font-size: 20px;
    line-height: 24px;
  }
  .person-role {
    font-style: italic;
    font-size: 12px;
    color: var(--icon);
    line-height: 14px;
  }
  .address {
    margin-top: 90px;
    font-size: 13px;
    line-height: 18px;
  }
  .contact-list { list-style: none; margin-top: 10px; font-size: 13px; }
  .contact-list li {
    display: flex;
    justify-content: flex-end;
    align-items: center;
    gap: 8px;
    height: 18.5px;
  }
  .contact-list svg { width: 11px; height: 11px; fill: var(--icon); flex: none; }
</style>
</head>
<body>
  <section class="card card-front" aria-label="Business card front">
    <div class="brand-name">BrightNest Mums</div>
    <div class="strapline">TAP | GATHER | SORTED</div>
  </section>

  <section class="card card-back" aria-label="Business card back">
    <svg class="back-panel" width="484" height="292" viewBox="0 0 484 292">
      <path d="M0 0 H202 Q262 146 210 292 H0 Z" fill="var(--teal-light)"/>
      <path d="M0 0 H196 Q254 146 203 292 H0 Z" fill="var(--teal-deep)"/>
      <circle cx="115" cy="144" r="52" fill="#fff"/>
    </svg>
    <div class="contact-block">
      <div class="person-name">Lena Forbisher</div>
      <div class="person-role">Founder</div>
      <div class="address">47 Kowhai Terrace, Ellerslie,<br>Auckland 1051, New Zealand</div>
      <ul class="contact-list">
        <li>021 483 517
          <svg viewBox="0 0 12 12"><path d="M3 0h6a1 1 0 0 1 1 1v10a1 1 0 0 1-1 1H3a1 1 0 0 1-1-1V1a1 1 0 0 1 1-1zm0 1.5v8h6v-8zM6 10.2a.6.6 0 1 0 0 1.2.6.6 0 0 0 0-1.2z"/></svg>
        </li>
        <li>+64 (0)9 571 4860
          <svg viewBox="0 0 12 12"><path d="M1 4c0-1.5 2.2-2.5 5-2.5S11 2.5 11 4v1H8.5V4h-5v1H1zM3 6h6l1.5 4.5h-9z"/></svg>
        </li>
        <li>www.BrightNestMums.example
          <svg viewBox="0 0 12 12"><path d="M0 2h12v8H0zM1 3v.3l5 3.2 5-3.2V3z"/></svg>
        </li>
        <li>lena@brightnestmums.example
          <svg viewBox="0 0 12 12"><path d="M6 0a6 6 0 1 0 0 12A6 6 0 0 0 6 0zm-1 1.2C4.3 2.2 4 3.6 3.9 5.4H1.3A4.8 4.8 0 0 1 5 1.2zm2 0a4.8 4.8 0 0 1 3.7 4.2H8.1C8 3.6 7.7 2.2 7 1.2zM5.1 5.4c.1-1.7.5-3 .9-3.8.4.8.8 2.1.9 3.8zm-3.8 1.2h2.6c.1 1.8.4 3.2 1.1 4.2a4.8 4.8 0 0 1-3.7-4.2zm3.8 0h1.8c-.1 1.7-.5 3-.9 3.8-.4-.8-.8-2.1-.9-3.8zm3 0h2.6A4.8 4.8 0 0 1 7 10.8c.7-1 1-2.4 1.1-4.2z"/></svg>
        </li>
      </ul>
    </div>
  </section>
</body>
</html>
```